Corvel Capital LLC

Need Professional Business cards for New Investment Fund

Target Market(s)

High Quality investors

Industry/Entity Type

Financial

Contact Information for Business Card

Phone Number +1 555 284 6190
Name Lukas Varenko
Title Fund Manager
email lv@FundCorvel.com
Website www.FundCorvel.com

Colors

Designer to choose colors to be used in the design.

Requirements
Must have
• Must have our Logo and all of the above. Must be made so lettering and loge can be raised

```html
<!DOCTYPE html>
<html lang="en">
<head>
<meta charset="utf-8">
<title>Orsavel – Business Card</title>
<link href="https://fonts.googleapis.com/css2?family=Mulish:wght@700&family=Questrial&display=swap" rel="stylesheet">
<style>
  :root {
    --stage: #272727;
    --paper: #ffffff;
    --forest: #434f42;
    --leaf: #5cb84a;
    --ink: #444a44;
    --tint-light: #f2f8f0;
    --tint-dark: #4c584b;
  }
  * { box-sizing: border-box; margin: 0; padding: 0; }
  html, body {
    width: 1200px; height: 686px; overflow: hidden;
    background: var(--stage);
    font-family: "Questrial", "Century Gothic", sans-serif;
  }
  .card {
    position: absolute; top: 208px;
    width: 469px; height: 268px;
    overflow: hidden;
    box-shadow: 0 1px 3px rgba(0,0,0,.6);
  }
  .card--front { left: 118px; background: var(--paper); }
  .card--back { left: 613px; background: var(--forest); }

  .brand {
    position: absolute; display: flex; align-items: center; gap: 7px;
    font-family: "Mulish", "Century Gothic", sans-serif;
    font-weight: 700; letter-spacing: 0.1em; line-height: 1;
  }
  .brand__mark { display: block; width: 10px; height: 10px; background: var(--leaf); }
  .card--front .brand { left: 30px; top: 44px; font-size: 17px; color: var(--forest); }
  .card--back .brand {
    left: 50%; top: 50%; transform: translate(-50%, -50%);
    font-size: 26px; color: #ffffff; gap: 10px;
  }
  .card--back .brand__mark { width: 15px; height: 15px; }

  .decor { position: absolute; display: block; }
  .card--front .decor { right: 18px; top: 0; width: 24px; height: 198px; background: var(--tint-light); }
  .card--back .decor { left: 18px; top: 71px; width: 24px; height: 197px; background: var(--tint-dark); }

  .holder { position: absolute; left: 30px; top: 154px; }
  .holder__name {
    font-family: "Mulish", "Century Gothic", sans-serif;
    font-size: 17.5px; font-weight: 700; letter-spacing: 0.05em;
    color: var(--leaf); text-transform: uppercase; line-height: 1.15;
  }
  .holder__title { margin-top: 1px; font-size: 12.5px; line-height: 1.1; color: var(--ink); letter-spacing: 0.05em; }

  .contacts { position: absolute; left: 30px; top: 205px; list-style: none; }
  .contacts__item {
    display: flex; align-items: center; height: 14.6px;
    font-size: 12.5px; color: var(--ink); letter-spacing: 0.05em;
  }
  .contacts__icon { width: 10px; height: 10px; margin-right: 8px; flex: none; }
</style>
</head>
<body>
  <section class="card card--front">
    <span class="decor" aria-hidden="true"></span>
    <div class="brand"><span class="brand__mark"></span>ORSAVEL</div>

    <div class="holder">
      <h1 class="holder__name">Lukas Varenko</h1>
      <p class="holder__title">Fund Manager</p>
    </div>

    <ul class="contacts">
      <li class="contacts__item">
        <svg class="contacts__icon" viewBox="0 0 10 10" aria-hidden="true">
          <path d="M2 0.5 L3.6 2.8 L2.7 3.8 Q4 6.3 6.2 7.3 L7.2 6.4 L9.5 8 L8.3 9.5 Q2.5 8.5 0.5 1.7 Z" fill="#5cb84a"/>
        </svg>+1 555 284 6190</li>
      <li class="contacts__item">
        <svg class="contacts__icon" viewBox="0 0 10 10" aria-hidden="true">
          <rect x="0.7" y="2" width="8.6" height="6.2" fill="none" stroke="#5cb84a" stroke-width="1"/>
          <path d="M0.9 2.3 L5 5.5 L9.1 2.3" fill="none" stroke="#5cb84a" stroke-width="1"/>
        </svg>lv@FundCorvel.com</li>
      <li class="contacts__item">
        <svg class="contacts__icon" viewBox="0 0 10 10" aria-hidden="true">
          <g fill="none" stroke="#5cb84a" stroke-width="0.8">
            <circle cx="5" cy="5" r="4.3"/>
            <ellipse cx="5" cy="5" rx="1.8" ry="4.3"/>
            <path d="M0.7 5 H9.3 M1.5 2.8 H8.5 M1.5 7.2 H8.5"/>
          </g>
        </svg>www.FundCorvel.com</li>
    </ul>
  </section>

  <section class="card card--back">
    <span class="decor" aria-hidden="true"></span>
    <div class="brand"><span class="brand__mark"></span>ORSAVEL</div>
  </section>
</body>
</html>
```